Business Card and Letterhead for Pimlu - modern real estate business

I need a double sided business card design for Pimlu. Please see business card brief here https://files.trelvonadocs.com/sheet/r/7QzTmWbaXLJnoPEd-kRyUgFhHsstbvCe2qfoMxDa_pz/view?mode=shared

Please feel free to design the business cards however you feel best. I am happy to give some creative freedoms and then provide feedback from there.

Please then also create a letterhead to match the business card design

Colors

Designer to choose colors to be used in the design.

Requirements
Must have
• Must be a modern, elegant business card which looks very professional

```html
<!DOCTYPE html>
<html lang="en">
<head>
<meta charset="utf-8">
<title>Pimlu – Business Card</title>
<link rel="stylesheet" href="https://fonts.googleapis.com/css2?family=Michroma&family=Montserrat:wght@400;500;600&display=swap">
<style>
  :root {
    --page-bg: #e9e6e3;
    --card-bg: #262427;
    --card-edge: #1c1a1d;
    --brand-red: #e3101b;
    --text-light: #f2f2f2;
    --photo-top: #3a383b;
    --photo-bottom: #1f1e20;
  }
  * { box-sizing: border-box; margin: 0; padding: 0; }
  html, body {
    width: 1200px; height: 800px; overflow: hidden;
    background: var(--page-bg);
  }
  .sheet {
    position: relative; width: 1200px; height: 800px;
    display: flex; align-items: center; justify-content: center; gap: 60px;
  }
  .card {
    position: relative; width: 520px; height: 298px;
    background: var(--card-bg);
    box-shadow: 0 10px 28px rgba(0,0,0,.25);
    overflow: hidden;
  }
  .card__stripe {
    position: absolute; left: 0; right: 0; bottom: 0; height: 7px;
    background: var(--brand-red);
  }
  /* Front */
  .card--front { display: flex; align-items: center; justify-content: center; }
  .brand-name {
    font-family: "Michroma", "Montserrat", sans-serif;
    font-weight: 400; font-size: 62px; letter-spacing: 4px;
    color: var(--brand-red); text-transform: uppercase;
    margin-bottom: 10px;
  }
  /* Back */
  .agent {
    position: absolute; left: 30px; top: 32px;
  }
  .agent__name {
    font-family: "Michroma", "Montserrat", sans-serif;
    font-size: 23px; letter-spacing: 1.5px; color: var(--brand-red);
    text-transform: uppercase; line-height: 1.1;
  }
  .agent__role {
    font-family: "Montserrat", sans-serif; font-weight: 600;
    font-size: 14px; color: var(--text-light); margin-top: 3px;
  }
  .divider {
    position: absolute; left: 30px; width: 80px; height: 1px;
    background: var(--brand-red);
  }
  .divider--top { top: 98px; }
  .divider--bottom { top: 190px; }
  .contact-list {
    position: absolute; left: 30px; top: 112px; list-style: none;
    font-family: "Montserrat", sans-serif; font-size: 14px;
    color: var(--text-light); line-height: 21px;
  }
  .contact-list li { display: flex; align-items: center; gap: 8px; }
  .contact-list svg { width: 11px; height: 11px; flex: none; }
  .address {
    position: absolute; left: 30px; top: 204px;
    font-family: "Montserrat", sans-serif; font-size: 14px;
    color: var(--text-light); line-height: 21px; font-style: normal;
  }
  .agent-photo {
    position: absolute; right: 0; bottom: 0; width: 235px; height: 240px;
    background: linear-gradient(180deg, var(--photo-top), var(--photo-bottom));
  }
</style>
</head>
<body>
<main class="sheet">
  <section class="card card--front" aria-label="Business card front">
    <span class="brand-name">Pimlu</span>
    <div class="card__stripe"></div>
  </section>

  <section class="card card--back" aria-label="Business card back">
    <div class="agent">
      <h1 class="agent__name">Jordan Mercer</h1>
      <p class="agent__role">Licenced Real Estate Agent</p>
    </div>
    <div class="divider divider--top"></div>
    <ul class="contact-list">
      <li>
        <svg viewBox="0 0 12 12" aria-hidden="true"><path fill="var(--brand-red)" d="M2.5 0.8l2 2-1 1.3c.6 1.5 1.9 2.8 3.4 3.4l1.3-1 2 2-1.3 1.5C5.6 9.8 2.2 6.4 1 2.1z"/></svg>
        0455 318 902
      </li>
      <li>
        <svg viewBox="0 0 12 12" aria-hidden="true"><rect x="0.5" y="2" width="11" height="8" rx="1" fill="var(--brand-red)"/><path d="M1 2.8l5 3.6 5-3.6" stroke="var(--card-bg)" stroke-width="1" fill="none"/></svg>
        jordan@pimlu.com
      </li>
      <li>
        <svg viewBox="0 0 12 12" aria-hidden="true"><circle cx="6" cy="6" r="5.5" fill="var(--brand-red)"/><path d="M0.8 6h10.4M6 0.5c-2.6 3-2.6 8 0 11M6 0.5c2.6 3 2.6 8 0 11" stroke="var(--card-bg)" stroke-width="0.8" fill="none"/></svg>
        www.pimlu.com
      </li>
    </ul>
    <div class="divider divider--bottom"></div>
    <address class="address">PO Box 6130<br>Ashgrove Ridge NSW 2791</address>
    <div class="card__stripe"></div>
    <div class="agent-photo" role="img" aria-label="Portrait photo of the agent in a dark suit"></div>
  </section>
</main>
</body>
</html>
```